Marrowby Water Taxi and Transport Business Card

I need business cards for my new water taxi and freight transport business I have started here in Kodiak Alaska. Kodiak is a remote island in the middle of the gulf of Alaska. There are seven native villages around the island and Kodiak is the #2 fishing port in the United States. We also have the largest Coast Guard Base in the U.S. My company will be providing water taxi and freight transport logistics to the villages and many hunting and fishing lodges as well as remote properties around the island.

I would like a business card that isn't status quo, something that stands out, either in feel or appearance. I do like clean minimal designs but it needs to have the necessary contact info on it.

Target Market(s)

remote lodge / property owners, residents of the many villages around Kodiak and any one wanting to enjoy the great outdoors of Kodiak Alaska

Industry/Entity Type

Business

Contact Information for Business Card

I like clean simple designs that aren't cluttered but still provide the necessary information

Colors
0255a3
3277b5
33a4d5
9bcb3c
add136
fbed22
ffc214
f78f20
f37122

Requirements
Must have
• logo and contact info
• Captain Mason Elwick
• www.marrowbyferryline.com
• mason@marrowbyferryline.com

```html
<!DOCTYPE html>
<html lang="en">
<head>
<meta charset="utf-8">
<title>Marrowby Water Taxi and Transport – Business Card</title>
<link rel="stylesheet" href="https://fonts.googleapis.com/css2?family=Montserrat:wght@400;500;700&display=swap">
<style>
  :root {
    --page-bg: #e7e3de;
    --card-top: #f4f5f6;
    --card-top-edge: #e2e6ea;
    --band-dark: #0d2357;
    --band-mid: #173f86;
    --band-light: #2a63ad;
    --band-rule: #3277b5;
    --brand-blue: #0255a3;
    --accent-orange: #f37122;
    --title-grey: #a9b3c2;
    --contact-text: #dfe6f1;
  }
  * { box-sizing: border-box; margin: 0; padding: 0; }
  html, body {
    width: 1200px;
    height: 969px;
    overflow: hidden;
    background: var(--page-bg);
    font-family: "Montserrat", sans-serif;
  }
  .canvas {
    position: relative;
    width: 1200px;
    height: 969px;
  }
  .business-card {
    position: absolute;
    left: 100px;
    top: 200px;
    width: 1000px;
    height: 570px;
    border-radius: 28px;
    overflow: hidden;
    background: linear-gradient(180deg, var(--card-top) 0%, var(--card-top-edge) 100%);
    box-shadow: 0 18px 40px rgba(40, 40, 50, 0.18);
  }
  .brand-block {
    position: absolute;
    left: 0;
    right: 0;
    top: 110px;
    text-align: center;
    color: var(--brand-blue);
    font-weight: 700;
  }
  .brand-mark {
    display: inline-block;
    width: 34px;
    height: 34px;
    border-radius: 50%;
    background: var(--accent-orange);
    margin-bottom: 18px;
  }
  .brand-name {
    font-size: 74px;
    letter-spacing: 2px;
    line-height: 1;
    text-transform: uppercase;
  }
  .brand-tagline {
    font-size: 26px;
    margin-top: 10px;
    letter-spacing: 0.5px;
  }
  .contact-band {
    position: absolute;
    left: 0;
    right: 0;
    bottom: 0;
    height: 222px;
    background: linear-gradient(90deg, var(--band-mid) 0%, var(--band-light) 30%, var(--band-mid) 65%, var(--band-dark) 100%);
    border-top: 4px solid var(--band-rule);
  }
  .holder {
    position: absolute;
    left: 0;
    width: 470px;
    top: 84px;
    text-align: right;
  }
  .holder-name {
    color: var(--accent-orange);
    font-size: 34px;
    font-weight: 500;
    letter-spacing: 1px;
    text-transform: uppercase;
  }
  .holder-title {
    color: var(--title-grey);
    font-size: 27px;
    margin-top: 8px;
  }
  .divider {
    position: absolute;
    left: 497px;
    top: 70px;
    width: 2px;
    height: 105px;
    background: var(--accent-orange);
  }
  .contact-list {
    position: absolute;
    left: 530px;
    top: 68px;
    list-style: none;
  }
  .contact-item {
    display: flex;
    align-items: center;
    gap: 22px;
    height: 38px;
    color: var(--contact-text);
    font-size: 24px;
  }
  .contact-icon {
    width: 22px;
    height: 22px;
    flex: none;
    fill: var(--accent-orange);
  }
</style>
</head>
<body>
<main class="canvas">
  <section class="business-card" aria-label="Marrowby Water Taxi and Transport business card">
    <div class="brand-block">
      <span class="brand-mark" aria-hidden="true"></span>
      <div class="brand-name">Marrowby</div>
      <div class="brand-tagline">Water Taxi &amp; Transport</div>
    </div>

    <div class="contact-band">
      <div class="holder">
        <div class="holder-name">Mason Elwick</div>
        <div class="holder-title">Captain</div>
      </div>
      <div class="divider"></div>
      <ul class="contact-list">
        <li class="contact-item">
          <svg class="contact-icon" viewBox="0 0 24 24" aria-hidden="true">
            <path d="M6.6 10.8a15.2 15.2 0 0 0 6.6 6.6l2.2-2.2a1 1 0 0 1 1-.25 11.4 11.4 0 0 0 3.6.57 1 1 0 0 1 1 1V20a1 1 0 0 1-1 1A17 17 0 0 1 3 4a1 1 0 0 1 1-1h3.5a1 1 0 0 1 1 1c0 1.25.2 2.45.57 3.57a1 1 0 0 1-.25 1z"/>
          </svg>
          <span>555 204 7316</span>
        </li>
        <li class="contact-item">
          <svg class="contact-icon" viewBox="0 0 24 24" aria-hidden="true">
            <path d="M2 5h20v14H2z M3.5 6.5 12 13l8.5-6.5" fill="none" stroke="#f37122" stroke-width="0"/>
            <path d="M2 5h20v2.2l-10 6.6L2 7.2z"/>
            <path d="M2 9.4l10 6.6 10-6.6V19H2z"/>
          </svg>
          <span>mason@marrowbyferryline.com</span>
        </li>
        <li class="contact-item">
          <svg class="contact-icon" viewBox="0 0 24 24" aria-hidden="true">
            <circle cx="12" cy="12" r="10"/>
            <path d="M12 2v20M2 12h20M5 6.5c4 2 10 2 14 0M5 17.5c4-2 10-2 14 0" fill="none" stroke="#173f86" stroke-width="1.4"/>
            <ellipse cx="12" cy="12" rx="4.5" ry="10" fill="none" stroke="#173f86" stroke-width="1.4"/>
          </svg>
          <span>marrowbyferryline.com</span>
        </li>
      </ul>
    </div>
  </section>
</main>
</body>
</html>
```